Quillmoor Climate Business Card Design

Design new, 2 sides, business cards for a residential and light commercial heating, air conditioning contractor.

Target Market(s)

Homeowners, small businesses

Industry/Entity Type

Business

Contact Information for Business Card

Dominic Westerhall
Phone - 862-415-2736
Email
Address - PO box 518
Brightwater NJ 07912
Website - www.HarborBreezeLLC.example

Requirements
Must have
• logo, company colors, standard size with no die cut, so I can use nova stamp

```html
<!DOCTYPE html>
<html lang="en">
<head>
<meta charset="utf-8">
<title>Quillmoor Climate Business Card</title>
<link rel="stylesheet" href="https://fonts.googleapis.com/css2?family=Roboto:wght@400;500;700&family=Roboto+Condensed:wght@700&display=swap">
<style>
  :root {
    --bg: #e4e4e4;
    --maroon: #7a2a2d;
    --maroon-deep: #6a1f25;
    --gold: #e0b313;
    --cream: #f6e7b0;
    --orange: #d9801d;
    --red: #c1341d;
    --paper: #f7f7f5;
    --ink: #2b1a1a;
    --rule: #e8bd3a;
  }
  * { margin: 0; padding: 0; box-sizing: border-box; }
  html, body { width: 1200px; height: 576px; overflow: hidden; }
  body {
    background: var(--bg);
    font-family: "Roboto", Arial, sans-serif;
    position: relative;
  }
  .card {
    position: absolute;
    top: 138px;
    box-shadow: 0 2px 5px rgba(0,0,0,0.3);
    overflow: hidden;
  }
  .card-front {
    left: 81px; width: 485px; height: 294px;
    background: var(--maroon);
  }
  .front-brand {
    position: absolute; left: 0; right: 0; top: 112px;
    text-align: center;
    font-family: "Roboto Condensed", "Roboto", sans-serif;
    font-weight: 700; font-size: 40px;
    color: var(--cream);
  }
  .front-band {
    position: absolute; left: 0; right: 0; top: 249px; height: 22px;
    background: var(--gold);
    display: flex; align-items: center; justify-content: center;
    font-size: 12px; color: var(--ink);
  }
  .card-back {
    left: 602px; width: 481px; height: 292px;
    background: var(--paper);
  }
  .back-brand {
    position: absolute; left: 26px; top: 62px;
    display: flex; align-items: center; gap: 8px;
    font-family: "Roboto Condensed", "Roboto", sans-serif;
    font-weight: 700; font-size: 26px;
    color: var(--maroon-deep);
  }
  .back-brand .mark {
    width: 14px; height: 14px; border-radius: 50%;
    background: var(--orange);
  }
  .holder {
    position: absolute; right: 25px; top: 138px; text-align: right;
  }
  .holder-name {
    font-family: "Roboto Condensed", "Roboto", sans-serif;
    font-weight: 700; font-size: 21px; color: var(--maroon-deep);
    line-height: 26px;
  }
  .holder-title { font-size: 11px; color: var(--ink); margin-top: 1px; }
  .holder-rule {
    position: absolute; left: 25px; top: 177px; width: 336px; height: 1px;
    background: var(--rule);
  }
  .contacts {
    position: absolute; left: 25px; top: 200px; list-style: none;
  }
  .contacts li {
    display: flex; align-items: center; gap: 12px;
    height: 18.5px; font-size: 13px; color: var(--ink);
  }
  .contacts svg { width: 12px; height: 12px; fill: var(--red); }
  .band-orange {
    position: absolute; left: 0; bottom: 0; width: 270px; height: 17px;
    background: var(--orange);
  }
  .band-web {
    position: absolute; right: 0; bottom: 0; width: 227px; height: 35px;
    background: var(--red);
    clip-path: polygon(16px 0, 100% 0, 100% 100%, 0 100%);
    color: #fff; font-size: 13px;
    display: flex; align-items: center; justify-content: flex-end;
    padding-right: 24px;
  }
</style>
</head>
<body>
  <section class="card card-front" aria-label="Card front">
    <div class="front-brand">Quillmoor Climate</div>
    <div class="front-band">Residential &amp; Light Commercial Heating &nbsp;•&nbsp;Air Conditioning Contractor</div>
  </section>

  <section class="card card-back" aria-label="Card back">
    <div class="back-brand"><span class="mark"></span>Quillmoor Climate</div>
    <div class="holder">
      <div class="holder-name">Dominic Westerhall</div>
      <div class="holder-title">Managing Director</div>
    </div>
    <div class="holder-rule"></div>
    <ul class="contacts">
      <li><svg viewBox="0 0 12 12"><path d="M1 4c0-2 2-3 5-3s5 1 5 3v1H8.5V3.8H3.5V5H1z M2.5 6h7l1 5h-9z"/></svg>862-415-2736</li>
      <li><svg viewBox="0 0 12 12"><path d="M0 2h12v8H0z M1 3l5 4 5-4v-.5H1z" fill-rule="evenodd"/></svg>info@QuillmoorClimateLLC.example</li>
      <li><svg viewBox="0 0 12 12"><path d="M6 0a4 4 0 0 1 4 4c0 3-4 8-4 8S2 7 2 4a4 4 0 0 1 4-4zm0 2.3a1.7 1.7 0 1 0 0 3.4 1.7 1.7 0 0 0 0-3.4z"/></svg>PO box 518 Brightwater NJ 07912</li>
    </ul>
    <div class="band-orange"></div>
    <div class="band-web">QuillmoorClimateLLC.example</div>
  </section>
</body>
</html>
```